Real Estate Company Looking for Business Card Designs for 3 Executives

Hello!
Thanks so much for considering our project! We are a real estate investment company located in Edmonton, Alberta called Bellhaven Group of Companies. We invest/develop both commercial and residential real estate and are looking to create 3 DOUBLE-SIDED business cards for 3 top executives in the company! (for some reason it won't let us select the double-sided option, but yes, the cards are double sided and would be happy to tip extra)

We have certain guidelines that we want our business cards to for sure follow - the back of the Business card has to be the Black Background Version of the Logo which has already been designed and linked as a file (first file). We want the entire back of the card to simply just be the black background logo. In terms of the front of the card, would like to see a smaller version of the white background logo (linked as the second file) in the top left hand corner - of course, feel free to get creative and we can make revisions together along the way! and Then after that, just text. We want the card to be sharp, clean, easy on the eyes and highly professional looking. We would like the card to include the Full name of the Company (Bellhaven Group of Companies), Name of the Person, Title, Phone, Email. If possible please provide the front part of the card for 3 people:

1) Bellhaven Group of Companies, Liora Quenby, Chief Financial Officer, 780-555-0142, lioraquenby@bellhavengroup.example

2) Bellhaven Group of Companies, Tobias Quenby, Chief Executive Officer, 780-555-0187, tobiasquenby@bellhavengroup.example

3) Bellhaven Group of Companies, Rui Delcourt, Chief Operations Officer, 587-555-0163, ruidelcourt@bellhavengroup.example

Thank you so much for considering our project & we look forward to seeing your designs!

```html
<!DOCTYPE html>
<html lang="en">
<head>
<meta charset="utf-8">
<title>Bellhaven Group of Companies — Business Card</title>
<link rel="stylesheet" href="https://fonts.googleapis.com/css2?family=Arimo:wght@400&family=Tinos:wght@700&display=swap">
<style>
  :root {
    --backdrop: #2b2b2b;
    --card: #1e1e1e;
    --ink: #ffffff;
  }
  * { margin: 0; padding: 0; box-sizing: border-box; }
  html, body {
    width: 1200px; height: 1059px; overflow: hidden;
    background: var(--backdrop);
  }
  .canvas { position: relative; width: 1200px; height: 1059px; }
  .card {
    position: absolute;
    background: var(--card);
    color: var(--ink);
  }
  .card--front { left: 257px; top: 89px; width: 687px; height: 390px; }
  .card--back  { left: 253px; top: 547px; width: 694px; height: 393px; }

  .wordmark {
    position: absolute;
    font-family: "Arimo", Arial, sans-serif;
    font-weight: 400;
    color: var(--ink);
    text-align: center;
    text-transform: uppercase;
  }
  .wordmark__name { display: block; letter-spacing: 0.32em; }
  .wordmark__sub { display: block; letter-spacing: 0.18em; }

  .card--front .wordmark { left: 70px; top: 150px; width: 240px; }
  .card--front .wordmark__name { font-size: 26px; margin-bottom: 8px; }
  .card--front .wordmark__sub { font-size: 11px; }

  .divider {
    position: absolute; left: 322px; top: 123px;
    width: 1px; height: 145px; background: var(--ink);
  }
  .person { position: absolute; left: 350px; top: 116px; }
  .person__name {
    font-family: "Tinos", "Times New Roman", serif;
    font-weight: 700; font-size: 27px; line-height: 1;
    letter-spacing: 0.01em; text-transform: uppercase;
  }
  .person__title {
    font-family: "Arimo", Arial, sans-serif;
    font-size: 16px; margin-top: 6px;
  }
  .contact {
    list-style: none; margin-top: 34px;
    font-family: "Arimo", Arial, sans-serif; font-size: 16px;
  }
  .contact li { display: flex; align-items: center; height: 26px; }
  .contact svg { width: 12px; height: 12px; margin-right: 8px; flex: none; }

  .card--back .wordmark { left: 0; top: 150px; width: 694px; }
  .card--back .wordmark__name { font-size: 40px; margin-bottom: 14px; }
  .card--back .wordmark__sub { font-size: 15px; }
</style>
</head>
<body>
<div class="canvas">
  <section class="card card--front">
    <div class="wordmark">
      <span class="wordmark__name">Bellhaven</span>
      <span class="wordmark__sub">Group of Companies</span>
    </div>
    <div class="divider"></div>
    <div class="person">
      <div class="person__name">Liora Quenby</div>
      <div class="person__title">Chief Financial Officer</div>
      <ul class="contact">
        <li>
          <svg viewBox="0 0 12 12" aria-hidden="true"><path fill="#fff" d="M2.4 1l2 2.3-1.1 1.3c.7 1.5 1.8 2.6 3.3 3.3l1.3-1.1 2.3 2-1.3 1.6C4.6 10.2 1.8 7.4 1 3.1z"/></svg>
          780-555-0142
        </li>
        <li>
          <svg viewBox="0 0 12 12" aria-hidden="true"><rect x="0.5" y="2.5" width="11" height="7.5" fill="#fff"/><path d="M0.8 2.8L6 7l5.2-4.2" fill="none" stroke="#1e1e1e" stroke-width="1"/></svg>
          lioraquenby@bellhavengroup.example
        </li>
        <li>
          <svg viewBox="0 0 12 12" aria-hidden="true"><circle cx="6" cy="6" r="5.5" fill="#fff"/><path d="M6 .5v11M.5 6h11M2 3c2.5 1 5.5 1 8 0M2 9c2.5-1 5.5-1 8 0" fill="none" stroke="#1e1e1e" stroke-width="0.8"/></svg>
          www.bellhavengroup.example
        </li>
      </ul>
    </div>
  </section>

  <section class="card card--back">
    <div class="wordmark">
      <span class="wordmark__name">Bellhaven</span>
      <span class="wordmark__sub">Group of Companies</span>
    </div>
  </section>
</div>
</body>
</html>
```